Marlowe Group needs a business card

I would like the card to be simple but modern and elegant.
I like black and white.
or black and gold.
we are a private finance lender and also are involved in property and property developments.

please look at the business card photos i provided i would like M.G only one one side and all the other details on the other side use fonts that tie in with my theme.

Industry/Entity Type

Finance

Contact Information for Business Card

Marlowe Group (M.G) Daniel Marlowe M: 0413586207 E: danmarl@inboxmail.test

Font styles to use
Other font styles liked:
• Use fonts that would reflect our business

Colors
000000
ffffff

Requirements
Must have
• one side of details
• other side has either M.G or Marlowe Group like in the photos provided

```html
<!DOCTYPE html>
<html lang="en">
<head>
<meta charset="utf-8">
<title>Marlowe Group – Business Card</title>
<link rel="stylesheet" href="https://fonts.googleapis.com/css2?family=Cinzel:wght@400;700&family=Lato:wght@400&display=swap">
<style>
  :root {
    --backdrop: #6b6b6b;
    --card-light-top: #f4f4f4;
    --card-light-bottom: #e2e2e2;
    --card-dark: #000000;
    --ink: #111111;
    --paper: #ffffff;
    --rule: #9a9a9a;
  }
  html, body {
    margin: 0;
    padding: 0;
    width: 1200px;
    height: 900px;
    overflow: hidden;
    background: var(--backdrop);
  }
  .canvas {
    position: relative;
    width: 1200px;
    height: 900px;
  }
  .card {
    position: absolute;
    top: 271px;
    width: 457px;
    height: 281px;
    border-radius: 14px;
    box-shadow: 2px 3px 5px rgba(0,0,0,0.35);
    text-align: center;
    box-sizing: border-box;
  }
  .card--details {
    left: 137px;
    background: linear-gradient(160deg, var(--card-light-top), var(--card-light-bottom));
    color: var(--ink);
  }
  .card--brand {
    left: 626px;
    width: 458px;
    background: var(--card-dark);
    color: var(--paper);
  }
  .brand-mark {
    position: absolute;
    left: 50%;
    transform: translateX(-50%);
    font-family: "Cinzel", serif;
    font-weight: 400;
    letter-spacing: 4px;
    line-height: 1;
    white-space: nowrap;
  }
  .card--details .brand-mark {
    top: 58px;
    font-size: 58px;
  }
  .card--brand .brand-mark {
    top: 80px;
    font-size: 62px;
  }
  .holder-name {
    position: absolute;
    top: 183px;
    left: 0;
    right: 0;
    margin: 0;
    font-family: "Cinzel", serif;
    font-weight: 700;
    font-size: 16px;
    letter-spacing: 0.5px;
  }
  .holder-rule {
    position: absolute;
    top: 211px;
    left: 183px;
    width: 92px;
    height: 1px;
    background: var(--rule);
  }
  .contact-line {
    position: absolute;
    top: 221px;
    left: 0;
    right: 0;
    margin: 0;
    font-family: "Lato", sans-serif;
    font-size: 13px;
  }
  .contact-line .divider {
    margin: 0 4px 0 6px;
  }
  .group-name {
    position: absolute;
    top: 193px;
    left: 0;
    right: 0;
    margin: 0;
    font-family: "Cinzel", serif;
    font-weight: 400;
    font-size: 20px;
    letter-spacing: 1px;
  }
</style>
</head>
<body>
  <main class="canvas">
    <section class="card card--details" aria-label="Card front with contact details">
      <div class="brand-mark">M.G</div>
      <h1 class="holder-name">DANIEL MARLOWE</h1>
      <div class="holder-rule"></div>
      <p class="contact-line">M: 0413586207<span class="divider">|</span>E: danmarl@inboxmail.test</p>
    </section>

    <section class="card card--brand" aria-label="Card back with company name">
      <div class="brand-mark">M.G</div>
      <p class="group-name">Marlowe Group</p>
    </section>
  </main>
</body>
</html>
```